Heritage Hollow Business Cards

Require a business card design. <br/><br/>Needs to include logo (either round or long version) plus these details:<br/>Maya Torvell<br/>Heritage Hollow<br/>maya@kelvadtrading.com.au<br/>02 6481 7395<br/>PO Box Glenwarra NSW 2791<br/>www.heritagehollow.com.au<br/><br/>I need in an editable format so that I can create for multiple staff members. <br/><br/>

Target Market(s)

We are an online store selling renovation products to home owners are builders. Looking for a classic classy design.

Industry/Entity Type

Home And Garden

Contact Information for Business Card

Maya Torvell
Heritage Hollow
maya@kelvadtrading.com.au
02 6481 7395
PO Box Glenwarra NSW 2791
www.heritagehollow.com.au

Colors

Designer to choose colors to be used in the design.

Requirements
Must have
• Must include Logo.

```html
<!DOCTYPE html>
<html lang="en">
<head>
<meta charset="utf-8">
<title>Heritage Hollow Business Cards</title>
<link href="https://fonts.googleapis.com/css2?family=Open+Sans:wght@400;600&family=Raleway:wght@400;500&display=swap" rel="stylesheet">
<style>
  :root {
    --backdrop: #c0c0c0;
    --paper: #ffffff;
    --ink: #131317;
    --sage: #53715f;
    --text-light: #ffffff;
    --logo-ink: #1e1e1e;
  }
  * { margin: 0; padding: 0; box-sizing: border-box; }
  html, body {
    width: 912px; height: 1200px; overflow: hidden;
    background: var(--backdrop);
    font-family: "Open Sans", Arial, sans-serif;
  }
  .card {
    position: absolute;
    width: 538px; height: 308px;
    border-radius: 8px;
    overflow: hidden;
    background: var(--paper);
  }
  .card svg.card-shapes { position: absolute; inset: 0; }

  /* Front */
  .card-front { left: 194px; top: 210px; }
  .front-brand {
    position: absolute; left: 0; right: 0; top: 100px;
    text-align: center;
    font-size: 46px; font-weight: 600; color: var(--logo-ink);
    line-height: 1; white-space: nowrap;
  }
  .front-url {
    position: absolute; left: 0; right: 0; top: 266px;
    text-align: center;
    font-size: 15px; letter-spacing: 2px; color: var(--text-light);
    white-space: nowrap;
  }

  /* Back */
  .card-back { left: 201px; top: 620px; }
  .back-logo-ring {
    position: absolute; left: 42px; top: 53px;
    width: 194px; height: 194px;
    border: 1px solid var(--logo-ink); border-radius: 50%;
    display: flex; align-items: center; justify-content: center;
  }
  .back-brand {
    font-size: 30px; font-weight: 600; color: var(--logo-ink);
    line-height: 1.05; text-align: left;
  }
  .person {
    position: absolute; left: 328px; top: 26px;
    font-family: "Raleway", Arial, sans-serif;
    color: var(--text-light);
    white-space: nowrap;
  }
  .person-name {
    font-size: 26px; font-weight: 500; letter-spacing: 0.5px;
    line-height: 1;
  }
  .person-role {
    margin-top: 3px;
    font-size: 12px; line-height: 1.2;
  }
  .contact-list { list-style: none; }
  .contact-item {
    position: absolute; left: 268px;
    display: flex; align-items: center;
    height: 20px;
  }
  .contact-icon { width: 18px; height: 18px; }
  .contact-text {
    position: absolute; left: 44px; white-space: nowrap;
    font-size: 12px; color: var(--text-light);
  }
</style>
</head>
<body>

<section class="card card-front">
  <svg class="card-shapes" width="538" height="308" viewBox="0 0 538 308">
    <path fill="var(--sage)" d="M0,213 H282 V210 Q282,194 298,194 H538 V260 H0 Z"/>
    <rect fill="var(--ink)" x="0" y="252" width="538" height="56"/>
  </svg>
  <div class="front-brand">Heritage Hollow</div>
  <div class="front-url">www.heritagehollow.com.au</div>
</section>

<section class="card card-back">
  <svg class="card-shapes" width="538" height="308" viewBox="0 0 538 308">
    <rect fill="var(--ink)" x="257" y="0" width="281" height="308"/>
    <path fill="var(--sage)" d="M257,0 H272 V107 C288,107 296,116 296,130 V308 H257 Z"/>
    <path fill="var(--paper)" d="M257,246 C260,262 296,272 296,300 V308 H257 Z"/>
  </svg>

  <div class="back-logo-ring">
    <div class="back-brand">Heritage<br>Hollow</div>
  </div>

  <div class="person">
    <div class="person-name">MAYA TORVELL</div>
    <div class="person-role">Director</div>
  </div>

  <ul class="contact-list">
    <li class="contact-item" style="top:128px">
      <svg class="contact-icon" viewBox="0 0 24 24"><path fill="#fff" d="M6.6 10.8a15.1 15.1 0 0 0 6.6 6.6l2.2-2.2a1 1 0 0 1 1-.25 11.4 11.4 0 0 0 3.6.57 1 1 0 0 1 1 1V20a1 1 0 0 1-1 1A17 17 0 0 1 3 4a1 1 0 0 1 1-1h3.5a1 1 0 0 1 1 1c0 1.25.2 2.450.57 3.57a1 1 0 0 1-.25 1Z"/></svg>
      <span class="contact-text">02 6481 7395</span>
    </li>
    <li class="contact-item" style="top:159px">
      <svg class="contact-icon" viewBox="0 0 24 24"><rect x="2" y="5" width="20" height="14" fill="none" stroke="#fff" stroke-width="1.6"/><path d="M2 5l10 8 10-8M2 19l7.5-7M22 19l-7.5-7" fill="none" stroke="#fff" stroke-width="1.6"/></svg>
      <span class="contact-text">maya@kelvadtrading.com.au</span>
    </li>
    <li class="contact-item" style="top:192px">
      <svg class="contact-icon" viewBox="0 0 24 24"><circle cx="12" cy="12" r="9.5" fill="none" stroke="#fff" stroke-width="1.8"/><ellipse cx="12" cy="12" rx="4" ry="9.5" fill="none" stroke="#fff" stroke-width="1.4"/><path d="M2.5 12h19" stroke="#fff" stroke-width="1.4"/></svg>
      <span class="contact-text">www.heritagehollow.com.au</span>
    </li>
    <li class="contact-item" style="top:227px">
      <svg class="contact-icon" viewBox="0 0 24 24"><path fill="#fff" d="M12 2a7 7 0 0 0-7 7c0 5.2 7 13 7 13s7-7.8 7-13a7 7 0 0 0-7-7Zm0 9.5A2.5 2.5 0 1 1 12 6.5a2.5 2.5 0 0 1 0 5Z"/></svg>
      <span class="contact-text">PO Box Glenwarra NSW 2791</span>
    </li>
  </ul>
</section>

</body>
</html>
```